Falbrook Company Notepad / Grid pad / Graph pad

I need a "modern" version of this graph pad. The information at the top needs to be shown, along with the graph lines, however, I need this more "interesting" than it currently is. This will be printed and bound at the TOP edge with 50 sheets per pack.

Target Market(s)

Clients - Want to show sophistication and not childish.

Industry/Entity Type

Structural Engineering

Font styles to use
Sans Serif

Colors
0255a3
85abd2

Requirements
Must have
• My project must have all of the elements currently shown on the pdf
Should not have
• My project should not have clipart images.

Files

```html
<!DOCTYPE html>
<html lang="en">
<head>
<meta charset="utf-8">
<title>Falbrook Company Graph Pad</title>
<link rel="stylesheet" href="https://fonts.googleapis.com/css2?family=Source+Sans+3:wght@400;600&display=swap">
<style>
  :root {
    --paper: #f5f4f2;
    --ink-blue: #2a5a85;
    --brand-blue: #1f4e74;
    --brand-green: #1fa55a;
    --rule: #3b3b3b;
    --grid-line: #bdbdbd;
    --grid-frame: #6b6b6b;
    --white: #ffffff;
  }
  * { box-sizing: border-box; margin: 0; padding: 0; }
  html, body { width: 956px; height: 1200px; overflow: hidden; }
  body {
    background: var(--paper);
    font-family: "Source Sans 3", sans-serif;
    position: relative;
  }
  .brand { position: absolute; left: 62px; top: 89px; }
  .brand-name {
    display: flex; align-items: center; gap: 10px;
    font-size: 27px; font-weight: 600; letter-spacing: 0.5px;
    color: var(--brand-blue); line-height: 1;
  }
  .brand-dot { width: 14px; height: 14px; border-radius: 50%; background: var(--brand-green); }
  .field-label {
    position: absolute; font-size: 14px; color: var(--ink-blue); line-height: 1;
    transform: translateY(-50%);
  }
  .field-of { color: #222; }
  .field-line { position: absolute; height: 1px; background: var(--rule); }
  .grid { position: absolute; left: 68px; top: 215px; width: 820px; height: 864px; }
  .footer-bar {
    position: absolute; left: 67px; top: 1108px; width: 820px; height: 40px;
    background: var(--brand-blue); color: var(--white);
    display: flex; align-items: center; justify-content: center; gap: 12px;
    font-size: 14px; letter-spacing: 0.2px;
  }
  .contact { display: flex; align-items: center; gap: 5px; }
  .contact svg { width: 13px; height: 13px; fill: var(--white); }
</style>
</head>
<body>
  <div class="brand">
    <div class="brand-name"><span class="brand-dot"></span>FALBROOK COMPANY</div>
  </div>

  <span class="field-label" style="left:399px;top:72px">Project</span>
  <span class="field-line" style="left:453px;top:76px;width:180px"></span>
  <span class="field-label" style="left:645px;top:72px">Job No</span>
  <span class="field-line" style="left:702px;top:76px;width:181px"></span>

  <span class="field-label" style="left:402px;top:101px">Task</span>
  <span class="field-line" style="left:440px;top:105px;width:193px"></span>
  <span class="field-label" style="left:644px;top:101px">Author</span>
  <span class="field-line" style="left:702px;top:105px;width:181px"></span>

  <span class="field-label" style="left:402px;top:130px">Page</span>
  <span class="field-line" style="left:440px;top:135px;width:81px"></span>
  <span class="field-label field-of" style="left:529px;top:132px">of</span>
  <span class="field-line" style="left:550px;top:135px;width:83px"></span>
  <span class="field-label" style="left:659px;top:130px">Date</span>
  <span class="field-line" style="left:702px;top:135px;width:181px"></span>

  <svg class="grid" viewBox="0 0 820 864" aria-hidden="true">
    <defs>
      <pattern id="graph-cell" width="25.625" height="18.7826" patternUnits="userSpaceOnUse">
        <path d="M25.625 0V18.7826M0 18.7826H25.625" fill="none" stroke="var(--grid-line)" stroke-width="0.8"/>
      </pattern>
    </defs>
    <rect width="820" height="864" fill="url(#graph-cell)"/>
    <rect x="0.5" y="0.5" width="819" height="863" fill="none" stroke="var(--grid-frame)" stroke-width="1.2"/>
  </svg>

  <div class="footer-bar">
    <span class="contact">
      <svg viewBox="0 0 24 24"><path d="M12 2a7 7 0 0 0-7 7c0 5 7 13 7 13s7-8 7-13a7 7 0 0 0-7-7zm0 9.5A2.5 2.5 0 1 1 12 6.5a2.5 2.5 0 0 1 0 5z"/></svg>
      215 Marlow Avenue, Suite 302, Harbor City, FL 33100
    </span>
    <span class="contact">
      <svg viewBox="0 0 24 24"><path d="M6.6 10.8a15 15 0 0 0 6.6 6.6l2.2-2.2a1 1 0 0 1 1-.25 11.4 11.4 0 0 0 3.6.57 1 1 0 0 1 1 1V20a1 1 0 0 1-1 1A17 17 0 0 1 3 4a1 1 0 0 1 1-1h3.5a1 1 0 0 1 1 1c0 1.25.2 2.45.57 3.57a1 1 0 0 1-.25 1z"/></svg>
      555.014.2290
    </span>
    <span class="contact">
      <svg viewBox="0 0 24 24"><circle cx="12" cy="12" r="10"/><path d="M7 8c2 0 3 1 3 2.5S8 13 9 15s-1 4-1 4M15 5c-1 2 0 3 1.5 3.5S19 11 17 13s-1 4 0 5" stroke="var(--brand-blue)" stroke-width="2" fill="none"/></svg>
      www.falbrookcompany.com
    </span>
  </div>
</body>
</html>
```